Tovel & Associates - London New Letting and Property Management Company *

Tovel & Associates LTD is a new company based in London, and works with brand new residential property in the city centre.

We are aiming to have 1000 new properties a year.

We are looking for something modern and minimalistic :
Logo ,Monogram, Paper Head and Business Card.

Target Market(s)

Internation landlords

Industry/Entity Type

Real Estate

Logo Text

Tovel & Associates

Colors

Designer to choose colors to be used in the design.

Requirements
Nice to have
• A particular monogram with "TA"
Should not have
• Little House over the logo

```html
<!DOCTYPE html>
<html lang="en">
<head>
<meta charset="utf-8">
<title>Tovel &amp; Associates – Business Card</title>
<link href="https://fonts.googleapis.com/css2?family=Montserrat:wght@600&family=Work+Sans:wght@400;500&display=swap" rel="stylesheet">
<style>
  :root {
    --backdrop: #1c1c1d;
    --card: #262627;
    --card-edge: #2d2d2e;
    --silver: #9a9b9d;
    --accent: #1fa3e0;
    --brand-blue: #1f6fa3;
    --ink: #f1f1f1;
  }
  * { margin: 0; padding: 0; box-sizing: border-box; }
  html, body {
    width: 1200px; height: 900px; overflow: hidden;
    background: var(--backdrop);
  }
  .stage {
    position: relative; width: 1200px; height: 900px;
    display: flex; flex-direction: column; align-items: center; justify-content: center; gap: 36px;
  }
  .card {
    position: relative; width: 700px; height: 400px;
    background: var(--card);
    border: 1px solid var(--card-edge);
    font-family: "Work Sans", sans-serif;
  }
  /* front */
  .card-front { display: flex; align-items: center; justify-content: center; }
  .front-brand { display: flex; flex-direction: column; align-items: center; gap: 22px; }
  .brand-square { width: 64px; height: 64px; background: var(--silver); }
  .front-name {
    font-family: "Montserrat", sans-serif; font-weight: 600; font-size: 22px;
    letter-spacing: 3px; color: var(--silver);
  }
  /* back */
  .back-brand {
    position: absolute; right: 56px; top: 118px;
    font-family: "Montserrat", sans-serif; font-weight: 600; font-size: 17px;
    letter-spacing: 2px; color: var(--brand-blue);
  }
  .person { position: absolute; left: 64px; top: 150px; }
  .person-name {
    font-weight: 500; font-size: 30px; letter-spacing: 1.5px; color: var(--accent);
    line-height: 1;
  }
  .person-role { font-size: 17px; color: var(--ink); margin-top: 6px; }
  .divider {
    position: absolute; left: 56px; right: 56px; top: 232px;
    height: 2px; background: var(--accent);
  }
  .contacts {
    position: absolute; left: 56px; top: 252px; list-style: none;
    font-size: 18px; color: var(--ink); line-height: 28px;
  }
  .contacts li { display: flex; align-items: center; gap: 10px; }
  .contacts svg { width: 12px; height: 12px; flex: none; }
  .address {
    position: absolute; right: 56px; bottom: 40px;
    font-size: 18px; color: var(--ink); line-height: 26px; letter-spacing: 1px;
  }
</style>
</head>
<body>
<main class="stage">
  <section class="card card-front">
    <div class="front-brand">
      <div class="brand-square"></div>
      <div class="front-name">TOVEL &amp; ASSOCIATES</div>
    </div>
  </section>

  <section class="card card-back">
    <div class="back-brand">TOVEL &amp; ASSOCIATES</div>
    <div class="person">
      <div class="person-name">DANIEL HARROW</div>
      <div class="person-role">Director</div>
    </div>
    <div class="divider"></div>
    <ul class="contacts">
      <li>
        <svg viewBox="0 0 12 12" aria-hidden="true"><path d="M3 1 L5 1 L5.5 4 L4 5 Q5 7.5 7 8 L8 6.5 L11 7 L11 9 Q11 11 9 11 Q2 10 1 3 Q1 1 3 1 Z" fill="var(--accent)"/></svg>
        +44 20 7946 0321
      </li>
      <li>
        <svg viewBox="0 0 12 12" aria-hidden="true"><rect x="1" y="2.5" width="10" height="7" fill="none" stroke="var(--accent)" stroke-width="1.2"/><path d="M1 2.5 L6 6.5 L11 2.5" fill="none" stroke="var(--accent)" stroke-width="1.2"/></svg>
        info@tovel&amp;associates.com
      </li>
      <li>
        <svg viewBox="0 0 12 12" aria-hidden="true"><circle cx="6" cy="6" r="5" fill="none" stroke="var(--accent)" stroke-width="1.1"/><ellipse cx="6" cy="6" rx="2.2" ry="5" fill="none" stroke="var(--accent)" stroke-width="1"/><path d="M1 6 H11" stroke="var(--accent)" stroke-width="1"/></svg>
        www.tovel&amp;associates.com
      </li>
    </ul>
    <div class="address">
      14 Carrow Lane<br>London EC2A 4RT
    </div>
  </section>
</main>
</body>
</html>
```